Sticker for Scrap Metal Bin that is placed at customers premises

During the course of our operation, Scrap Metal Bin are place at our customer site for them to dispose scrap metal into the Bin.

Would like to have a sticker for us to paste on the bin.

All scrap bin will be blue color. Attached sample of current sticker on a scrap bin.

Would like one that is clean, simple and eye catching also that the font is much visible unlike the current one that is cramp and small.

Target Market(s)

Businesses

Font styles to use
Serif

Requirements
Must have
• 1) Company Name and Logo
• 2) Contact Details : 9413 5207 / 6582 3046
• 3) Website: www.korvamelt.com

```html
<!DOCTYPE html>
<html lang="en">
<head>
<meta charset="utf-8">
<title>Korva Melt Recycling – Scrap Metal Bin Sticker</title>
<link rel="stylesheet" href="https://fonts.googleapis.com/css2?family=Archivo:wdth,wght@125,700;125,800&family=Oswald:wght@500&display=swap">
<style>
  :root {
    --ink: #231f20;
    --signal-yellow: #fcd600;
    --paper: #ffffff;
    --backdrop: #d0d0d0;
  }
  * { margin: 0; padding: 0; box-sizing: border-box; }
  html, body {
    width: 1200px;
    height: 800px;
    overflow: hidden;
    background: var(--backdrop);
  }
  .sticker {
    position: absolute;
    left: 168px;
    top: 111px;
    width: 864px;
    height: 575px;
    background: var(--ink);
    font-family: "Archivo", "Arial", sans-serif;
    font-stretch: 125%;
  }
  .brand-mark {
    position: absolute;
    left: 384px;
    top: 39px;
    width: 106px;
    height: 104px;
    border: 5px solid var(--paper);
  }
  .brand-name {
    position: absolute;
    left: 0;
    width: 864px;
    top: 176px;
    text-align: center;
    color: var(--paper);
    font-weight: 800;
    line-height: 1;
  }
  .brand-name .name-main {
    display: block;
    font-size: 38px;
    letter-spacing: 1px;
  }
  .brand-name .name-sub {
    display: block;
    width: 372px;
    margin: 5px auto 0;
    text-align: right;
    font-size: 20px;
    letter-spacing: 1px;
  }
  .message-band {
    position: absolute;
    left: 0;
    top: 269px;
    width: 864px;
    height: 222px;
    background: var(--signal-yellow);
  }
  .recycle-icon {
    position: absolute;
    left: 41px;
    top: 15px;
    width: 186px;
    height: 186px;
    border-radius: 50%;
    background: radial-gradient(circle, var(--paper) 0 58%, var(--ink) 60%);
  }
  .band-divider {
    position: absolute;
    left: 244px;
    top: 18px;
    width: 5px;
    height: 197px;
    background: var(--ink);
  }
  .headline {
    position: absolute;
    left: 298px;
    top: 18px;
    color: var(--ink);
    font-weight: 700;
    font-size: 98px;
    line-height: 86px;
    letter-spacing: 1px;
  }
  .contact-bar {
    position: absolute;
    left: 0;
    top: 491px;
    width: 864px;
    height: 84px;
    display: flex;
    align-items: center;
    justify-content: space-between;
    padding: 0 44px 0 41px;
    color: var(--paper);
    font-family: "Oswald", "Arial Narrow", sans-serif;
    font-weight: 500;
    font-size: 30px;
  }
  .phone-line { display: flex; align-items: center; gap: 12px; }
  .phone-badge {
    width: 48px;
    height: 48px;
    border-radius: 50%;
    background: var(--signal-yellow);
    display: flex;
    align-items: center;
    justify-content: center;
  }
</style>
</head>
<body>
  <main class="sticker">
    <div class="brand-mark"></div>
    <h1 class="brand-name">
      <span class="name-main">KORVA MELT</span>
      <span class="name-sub">RECYCLING</span>
    </h1>

    <section class="message-band">
      <div class="recycle-icon" role="img" aria-label="Bolt inside circular recycling arrows"></div>
      <div class="band-divider"></div>
      <h2 class="headline">SCRAP<br>METAL</h2>
    </section>

    <footer class="contact-bar">
      <div class="phone-line">
        <span class="phone-badge">
          <svg width="24" height="24" viewBox="0 0 24 24" aria-hidden="true">
            <path fill="#231f20" d="M6.6 10.8c1.4 2.8 3.8 5.1 6.6 6.6l2.2-2.2c.3-.3.7-.4 1-.2 1.1.4 2.3.6 3.6.6.6 0 1 .4 1 1V20c0 .6-.4 1-1 1C10.6 21 3 13.4 3 4c0-.6.4-1 1-1h3.5c.6 0 1 .4 1 1 0 1.3.2 2.5.6 3.6.1.3 0 .7-.2 1z"/>
          </svg>
        </span>
        <span class="phone-numbers">:9413 5207 / 6582 3046</span>
      </div>
      <span class="website">www.korvamelt.com</span>
    </footer>
  </main>
</body>
</html>
```